Brightway Haul & Upkeep Services, are a company that offers a 'one stop shop' pre-move clean up a

I have already selected a logo which I would like on the front of the business cards along with phone numbers, web address and email which are:
0487650392
www.brightwayhaul.com.au
brightwayhaulandupkeep@mailbox.example

On the back of the card I would like to list some of the types of service we offer (clean - move - repairs/maintenance) which are:
CLEAN - windows, gutters, solar panels, driveways/paths, carpets.
MOVE - Small/medium size house/office moves, large item pick-up & delivery, yard clean-up and removal.
General maintenance and repairs.

I would like the blue logo on a gray background.

Thanks

```html
<!DOCTYPE html>
<html lang="en">
<head>
<meta charset="utf-8">
<title>Brightway Haul &amp; Upkeep Services – Business Card</title>
<link href="https://fonts.googleapis.com/css2?family=Open+Sans:wght@400;600;700;800&display=swap" rel="stylesheet">
<style>
  :root {
    --page: #efefef;
    --card-black: #050505;
    --brand-blue: #2a78c8;
    --deep-blue: #1d6cbf;
    --light-blue: #72b8ec;
    --card-grey: #dddddd;
    --card-grey-light: #e6e6e6;
    --divider: #b9b9b9;
    --ink: #1c1c1c;
    --white: #ffffff;
  }
  * { box-sizing: border-box; margin: 0; padding: 0; }
  html, body {
    width: 1016px; height: 1200px; overflow: hidden;
    background: var(--page);
    font-family: "Open Sans", Arial, sans-serif;
  }
  .sheet { position: relative; width: 1016px; height: 1200px; }
  .card {
    position: absolute; left: 28px; width: 960px; height: 547px; overflow: hidden;
  }
  /* Front */
  .card--front { top: 28px; background: var(--card-black); }
  .front-band {
    position: absolute; left: 0; right: 0; bottom: 0; height: 105px;
    background: linear-gradient(180deg, var(--light-blue) 0%, var(--deep-blue) 55%, var(--deep-blue) 100%);
  }
  .front-name {
    position: absolute; left: 92px; top: 150px;
    color: var(--brand-blue); font-weight: 800;
    font-size: 62px; line-height: 1.02; letter-spacing: 0.5px; text-transform: uppercase;
  }
  .front-name span { display: block; font-size: 38px; letter-spacing: 1px; }
  .front-phone {
    position: absolute; left: 106px; top: 372px;
    display: flex; align-items: center; gap: 12px;
    color: var(--white); font-size: 33px; font-weight: 400;
  }
  .front-phone svg { width: 28px; height: 28px; }
  .front-web {
    position: absolute; right: 18px; top: 458px;
    color: var(--white); font-size: 26px; font-weight: 400; letter-spacing: 0.3px;
  }
  .front-email {
    position: absolute; right: 18px; top: 502px;
    display: flex; align-items: center; gap: 8px;
    color: var(--white); font-size: 21px;
  }
  .front-email svg { width: 18px; height: 14px; }
  /* Back */
  .card--back {
    top: 625px;
    background: linear-gradient(180deg, var(--card-grey-light), var(--card-grey));
  }
  .back-brand {
    position: absolute; left: 30px; top: 180px; width: 460px; text-align: center;
  }
  .back-name {
    color: var(--brand-blue); font-weight: 800; text-transform: uppercase;
    font-size: 44px; line-height: 1.05;
  }
  .back-name span { display: block; font-size: 27px; letter-spacing: 0.5px; }
  .back-abn { margin-top: 22px; color: var(--ink); font-size: 30px; letter-spacing: 0.5px; }
  .back-divider {
    position: absolute; left: 518px; top: 52px; width: 2px; height: 448px;
    background: var(--divider);
  }
  .services { position: absolute; left: 550px; top: 48px; width: 400px; }
  .services-title { color: var(--brand-blue); font-size: 40px; font-weight: 600; margin-bottom: 20px; }
  .service { color: var(--ink); font-size: 26px; line-height: 1.3; margin-bottom: 20px; }
  .service-label { color: var(--brand-blue); font-weight: 700; }
  .service--general { color: var(--brand-blue); font-weight: 700; font-size: 29px; line-height: 1.2; }
</style>
</head>
<body>
<main class="sheet">
  <section class="card card--front" aria-label="Business card front">
    <div class="front-band" role="img" aria-label="Decorative blue wave band along the bottom of the card"></div>
    <h1 class="front-name">Brightway Haul<span>&amp; Upkeep Services</span></h1>
    <p class="front-phone">
      <svg viewBox="0 0 24 24" aria-hidden="true"><circle cx="12" cy="12" r="11" fill="none" stroke="#fff" stroke-width="1.8"/><path d="M8 6.5c-.8.6-1.3 1.5-1 2.7.8 3.3 3.6 6.2 6.9 7.1 1.1.3 2-.2 2.6-1l-2-1.8-1.2.9c-1.5-.7-2.7-1.9-3.4-3.4l.9-1.2Z" fill="#fff"/></svg>
      0487650392
    </p>
    <p class="front-web">www.brightwayhaul.com.au</p>
    <p class="front-email">
      <svg viewBox="0 0 18 14" aria-hidden="true"><rect x="0.5" y="0.5" width="17" height="13" rx="1.5" fill="#fff"/><path d="M1.5 2 L9 8 L16.5 2" fill="none" stroke="var(--deep-blue)" stroke-width="1.5"/></svg>
      brightwayhaulandupkeep@mailbox.example
    </p>
  </section>

  <section class="card card--back" aria-label="Business card back">
    <div class="back-brand">
      <h2 class="back-name">Brightway Haul<span>&amp; Upkeep Services</span></h2>
      <p class="back-abn">ABN 48519002736</p>
    </div>
    <div class="back-divider"></div>
    <div class="services">
      <h3 class="services-title">Services we offer</h3>
      <p class="service"><span class="service-label">CLEAN:</span> Windows, Gutters<br>Solar Panels, Driveways/paths,<br>Carpets.</p>
      <p class="service"><span class="service-label">MOVE:</span> Small/medium Size<br>House/office Moves,<br>Large Item Pick-up &amp; Delivery<br>Yard Clean-up And Removal.</p>
      <p class="service service--general">General maintenance and repairs.</p>
    </div>
  </section>
</main>
</body>
</html>
```